Stationery Design Project

I need a design that is simple, clean and modern, in square style, bold font.
The majority of the design needs to be White and Black with a splash of Red colour.
I would like a design for business cards and letter heads with the following information.
Name, Title, Phone, Fax, Email, Website and company ABN number

Target Market(s)

25 to 65 years old real estate clients

Industry/Entity Type

Business

Requirements
Must have
• All designs must incorporate Company Logo, Name, Title, Phone, Fax, Email, Website and company ABN number

```html
<!DOCTYPE html>
<html lang="en">
<head>
<meta charset="utf-8">
<title>Northgate Real Estate – Business Card</title>
<link rel="stylesheet" href="https://fonts.googleapis.com/css2?family=Open+Sans:wght@400;600;700&display=swap">
<style>
  :root {
    --red: #d7282b;
    --black: #1e1a1a;
    --white: #ffffff;
    --grey-text: #3a3a3a;
    --backdrop: #ececec;
  }
  * { box-sizing: border-box; margin: 0; padding: 0; }
  html, body {
    width: 1200px; height: 402px; overflow: hidden;
    background: var(--backdrop);
    font-family: "Open Sans", Arial, sans-serif;
  }
  .canvas { position: relative; width: 1200px; height: 402px; }

  .card { position: absolute; overflow: hidden; }
  .card-front { left: 73px; top: 55px; width: 511px; height: 292px; background: var(--white); }
  .card-back  { left: 625px; top: 50px; width: 513px; height: 291px; background: var(--red); }

  .card-curves { position: absolute; inset: 0; }

  .brand-frame {
    position: absolute; border-radius: 18px;
    display: flex; flex-direction: column; align-items: center; justify-content: center;
    font-weight: 700; text-align: center;
  }
  .card-front .brand-frame {
    left: 45px; top: 41px; width: 238px; height: 132px;
    border: 4px solid var(--black); color: var(--black);
  }
  .card-back .brand-frame {
    left: 106px; top: 45px; width: 303px; height: 166px;
    border: 5px solid var(--white); color: var(--white);
  }
  .brand-name { font-size: 34px; line-height: 1; letter-spacing: 1px; }
  .card-back .brand-name { font-size: 44px; }
  .brand-tagline { font-size: 11px; letter-spacing: 8px; margin-top: 10px; line-height: 1; }
  .card-back .brand-tagline { font-size: 14px; letter-spacing: 10px; margin-top: 14px; }

  .holder {
    position: absolute; left: 326px; top: 158px; width: 130px;
    padding-bottom: 4px; border-bottom: 2px solid var(--red);
    color: var(--red); font-size: 16px; font-weight: 700; white-space: nowrap;
  }
  .holder .title { font-weight: 400; font-size: 12px; color: var(--grey-text); }

  .address {
    position: absolute; right: 212px; top: 207px;
    text-align: right; font-size: 12px; line-height: 17px; color: var(--grey-text);
  }

  .contact-list {
    position: absolute; left: 326px; top: 207px; list-style: none;
    font-size: 12.5px; line-height: 16.7px; color: var(--grey-text);
  }
  .contact-list li { display: flex; align-items: center; gap: 5px; }
  .contact-list svg { width: 11px; height: 11px; fill: var(--red); flex: none; }

  .abn {
    position: absolute; left: 0; right: 0; top: 236px;
    text-align: center; color: var(--white); font-size: 15px;
  }
</style>
</head>
<body>
<div class="canvas">

  <section class="card card-front">
    <svg class="card-curves" viewBox="0 0 511 292" width="511" height="292" aria-hidden="true">
      <path d="M330 0 Q460 20 511 120 L511 0 Z" fill="var(--red)"/>
      <path d="M318 0 Q455 18 511 128" fill="none" stroke="var(--black)" stroke-width="3"/>
      <path d="M0 222 Q80 275 225 292 L0 292 Z" fill="var(--red)"/>
      <path d="M0 214 Q82 270 236 292" fill="none" stroke="var(--black)" stroke-width="3"/>
    </svg>

    <div class="brand-frame">
      <span class="brand-name">NORTHGATE</span>
      <span class="brand-tagline">REAL ESTATE</span>
    </div>

    <p class="holder">Your name, <span class="title">Title</span></p>

    <p class="address">Street Name, City Name<br>State, City Zip Code</p>

    <ul class="contact-list">
      <li><svg viewBox="0 0 12 12"><path d="M2.5 1 L4.5 1 L5 3.5 L3.8 4.5 Q5 7 7.5 8.2 L8.5 7 L11 7.5 L11 9.5 Q10 11 8 11 Q1 9 1 2.5 Q1 1 2.5 1Z"/></svg>123-456-7890</li>
      <li><svg viewBox="0 0 12 12"><rect x="3" y="1" width="6" height="4"/><rect x="1" y="5" width="10" height="5" rx="1"/><rect x="3" y="8" width="6" height="3" fill="var(--white)"/></svg>123-456-7890</li>
      <li><svg viewBox="0 0 12 12"><rect x="1" y="2.5" width="10" height="7" rx="1"/><path d="M1.5 3 L6 6.5 L10.5 3" fill="none" stroke="var(--white)" stroke-width="1"/></svg>info@mailbox.com</li>
      <li><svg viewBox="0 0 12 12"><circle cx="6" cy="6" r="5"/><path d="M1 6 H11 M6 1 Q3 6 6 11 M6 1 Q9 6 6 11" fill="none" stroke="var(--white)" stroke-width="0.8"/></svg>www.website.com</li>
    </ul>
  </section>

  <section class="card card-back">
    <div class="brand-frame">
      <span class="brand-name">NORTHGATE</span>
      <span class="brand-tagline">REAL ESTATE</span>
    </div>
    <p class="abn">ABN;123456789</p>
  </section>

</div>
</body>
</html>
```